Design a website for a newly developed Delta 8 THC Company

Design a responsive Website with the following goals in mind:
- Built on Wordpress/WooCommerce theme. Please use this when designing for ease of integration.
- Build trust with website visitors with an engaging, informative content driven website, that leads to a conversion of product purchase and repeat business. We will also be driving consumers to businesses that carry our products as well.
- The website will embody a lifestyle feel and make the visitor identify with the content.
- The website will allow for super charged SEO and other digital marketing and advertising strategies and tactics used to increase discovery, awareness, and conversion.
Please see additional goals in the uploaded files.
Target Market(s)
Male/Female 21-
Industry/Entity Type
Cannabis/Hemp
Coding
Coded - Design and coding required
Number of Pages Required
5+ page
Font styles to use
Other font styles liked:
- Montserrat
Look and feel
Each slider illustrates characteristics of the customer's brand and the style your logo design should communicate.

```html
<!DOCTYPE html>
<html lang="en">
<head>
<meta charset="utf-8">
<title>Aurelia — Delta 8 Premium Gummies</title>
<link href="https://fonts.googleapis.com/css2?family=Playfair+Display:wght@700;800&family=Poppins:wght@300;400;500;600&display=swap" rel="stylesheet">
<style>
:root{
  --gold-light:#f2e36c;
  --gold:#c9a13b;
  --gold-dark:#b8902f;
  --ink:#1d1d1d;
  --text:#555;
  --mute:#7a7a7a;
  --paper:#ffffff;
  --mist:#f4f4f4;
  --footer:#3a3a3c;
  --cherry:#c8373b;
  --berry:#1ea3de;
  --apple:#86b94a;
  --bag:#2b2b2b;
}
*{box-sizing:border-box;margin:0;padding:0}
html,body{width:1200px;height:3009px;overflow:hidden;background:var(--paper)}
body{position:relative;font-family:'Poppins',sans-serif;color:var(--text)}
.abs{position:absolute}
.serif{font-family:'Playfair Display',serif;font-weight:700;color:var(--ink)}
.gold-grad{background:linear-gradient(90deg,var(--gold-light),var(--gold-dark))}
.btn{position:absolute;display:flex;align-items:center;justify-content:center;border-radius:30px;font-size:10px;font-weight:600;color:var(--ink);text-transform:uppercase}
.btn-outline{border:1px solid var(--gold);background:var(--paper)}
.center{text-align:center;left:0;width:1200px}

.topbar{top:0;left:0;width:1200px;height:30px;display:flex;align-items:center;justify-content:center;font-size:11px;font-weight:500;color:var(--ink)}
.pattern{top:30px;left:625px;width:575px;height:486px;background:var(--mist)}
.brand{top:48px;left:157px;display:flex;align-items:center;gap:8px;font-size:15px;font-weight:600;letter-spacing:3px;color:var(--ink)}
.brand i{width:14px;height:14px;border-radius:50%;background:var(--gold)}
.nav{top:56px;left:665px;display:flex;gap:34px;font-size:11px;color:var(--ink)}
.hero-eyebrow{top:188px;left:157px;font-size:17px;color:var(--gold)}
.hero-title{top:212px;left:157px;font-size:42px;line-height:54px}
.hero-copy{top:328px;left:158px;width:290px;font-size:14px;line-height:20px}
.scroll{top:500px;left:157px;width:18px;height:30px;border:1px solid #ccc;border-radius:9px;font-size:11px;text-align:center;line-height:28px;color:#999}
.photo{background:linear-gradient(160deg,#f6d7a4,#e9a24a 55%,#7f8a4c)}
.bag{background:linear-gradient(180deg,#3a3a3a,var(--bag));border-radius:8px 8px 14px 14px;box-shadow:0 8px 14px rgba(0,0,0,.25)}

.about-band{top:680px;left:0;width:1200px;height:416px}
.about-frame{top:750px;left:155px;width:398px;height:410px;background:var(--paper);padding:9px}
.about-frame .photo{width:100%;height:100%;background:linear-gradient(170deg,#e8c48d,#9c8a4a 45%,#4a6a2e)}
.about-text{top:750px;left:610px;width:400px}
.about-title{font-size:36px;line-height:44px;color:var(--paper)}
.about-lead{margin-top:12px;font-size:12.5px;font-weight:600;line-height:22px;color:var(--paper)}
.about-copy{margin-top:8px;font-size:11.5px;line-height:20px;color:var(--paper)}
.about-text .read{position:relative;margin-top:22px;width:108px;height:31px;color:var(--gold);border:1px solid #fff;background:#fff}

.section-title{font-size:36px}
.section-copy{font-size:14px;line-height:25px;color:var(--text)}
.card-img{width:254px;height:248px;background:#efefef;overflow:hidden}
.card-img .bar{position:absolute;bottom:0;left:0;width:100%;height:7px}
.prod-name{font-size:17px;color:var(--ink);text-align:center;width:254px}
.prod-flavor{font-size:20px;text-align:center;width:254px;font-family:'Playfair Display',serif;font-weight:700}
.arrow{width:38px;height:38px;border-radius:50%;background:linear-gradient(90deg,var(--gold-light),var(--gold))}

.benefits{top:1823px;left:0;width:1200px;height:555px;background:var(--mist)}
.benefit{width:208px;height:224px;background:var(--paper);padding:28px 20px}
.benefit h3{font-family:'Playfair Display',serif;font-size:20px;color:var(--ink);margin:22px 0 10px}
.benefit p{font-size:11.5px;line-height:20px;color:var(--mute)}

.testimonial{top:2380px;left:0;width:1200px;height:272px}
.footer{top:2652px;left:0;width:1200px;height:307px;background:var(--footer);color:#ddd}
.copyright{top:2959px;left:0;width:1200px;height:50px;background:var(--mist);font-size:9px;color:var(--mute);display:flex;align-items:center;justify-content:center}
.social{width:38px;height:38px;border:1px solid #666;border-radius:50%}
.flink{font-size:12px;color:#e6e6e6}
</style>
</head>
<body>

<div class="abs topbar gold-grad">Aurelia Delta 8 Premium Gummies</div>
<div class="abs pattern" role="img" aria-label="Soft circular line pattern background"></div>
<div class="abs brand"><i></i>AURELIA</div>
<nav class="abs nav"><span>HOME</span><span>OUR STORY</span><span>SHOP</span><span>CONTACT US</span></nav>
<svg class="abs" style="top:55px;left:988px" width="16" height="16" viewBox="0 0 16 16" fill="none" stroke="#1d1d1d" stroke-width="1.6"><circle cx="6.5" cy="6.5" r="5"/><path d="M10.5 10.5l4 4"/></svg>
<svg class="abs" style="top:54px;left:1018px" width="22" height="20" viewBox="0 0 22 20" fill="none" stroke="#1d1d1d" stroke-width="1.5"><path d="M1 2h3l3 11h10l2-8H6"/><circle cx="8" cy="17" r="1.5"/><circle cx="16" cy="17" r="1.5"/><circle cx="19" cy="3" r="2.5" fill="#c9a13b" stroke="none"/></svg>

<div class="abs hero-eyebrow">AURELIA DELTA 8 PREMIUM GUMMIES</div>
<h1 class="abs serif hero-title">100% ORGANIC AND<br>ALL-NATURAL</h1>
<p class="abs hero-copy">Lorem ipsum dolor sit amet, consectetur adipiscing elit, sed do eiusmod</p>
<div class="btn gold-grad" style="top:402px;left:156px;width:130px;height:37px">Buy now</div>
<div class="abs scroll">↓</div>

<div class="abs photo" style="top:104px;left:587px;width:420px;height:456px" role="img" aria-label="Woman with raised arms in a sunlit meadow"></div>
<div class="abs bag" style="top:380px;left:499px;width:158px;height:230px" role="img" aria-label="Delta-8 gummies pouch"></div>
<div class="abs bag" style="top:395px;left:655px;width:120px;height:205px" role="img" aria-label="Delta-8 gummies pouch"></div>

<div class="abs about-band gold-grad"></div>
<div class="abs about-frame"><div class="photo" role="img" aria-label="Woman inspecting hemp plants at sunset"></div></div>
<div class="abs bag" style="top:1048px;left:455px;width:68px;height:110px" role="img" aria-label="Gummies pouch"></div>
<div class="abs bag" style="top:1058px;left:527px;width:56px;height:100px" role="img" aria-label="Gummies pouch"></div>
<div class="abs about-text">
  <h2 class="serif about-title">ABOUT OUR STORY</h2>
  <p class="about-lead">Lorem ipsum dolor sit amet, consectetuer adipiscing elit, sed diam nonummy nibh euismod tincidunt ut laoreet dolore.</p>
  <p class="about-copy">Lorem ipsum dolor sit amet, consectetuer adipiscing elit, sed diam nonummy nibh euismod tincidunt ut laoreet dolore magna aliquam erat volutpat. Ut wisi enim ad minim veniam, quis nostrud exerci tation ullamcorper suscipit lobortis nisl ut aliquip ex ea commodo consequat. Duis autem vel eum iriure dolor in hendrerit in vulputate velit esse molestie consequat.</p>
  <div class="btn read">Read more</div>
</div>

<h2 class="abs serif section-title center" style="top:1218px">OUR GUMMIES</h2>
<p class="abs section-copy center" style="top:1275px">Lorem ipsum dolor sit amet, consectetur adipiscing elit, sed do eiusmod<br>sum dolor sit amet, consectetung elit, sed do eiusmodsum dolor sit</p>

<div class="abs arrow" style="top:1494px;left:129px"><svg width="38" height="38" viewBox="0 0 38 38" fill="none" stroke="#1d1d1d" stroke-width="1.5"><path d="M25 19H13M17 15l-4 4 4 4"/></svg></div>
<div class="abs arrow" style="top:1494px;left:1033px"><svg width="38" height="38" viewBox="0 0 38 38" fill="none" stroke="#1d1d1d" stroke-width="1.5"><path d="M13 19h12M21 15l4 4-4 4"/></svg></div>

<div class="abs" style="top:1355px;left:190px">
  <div class="card-img" style="position:relative"><div class="abs bag" style="top:58px;left:47px;width:160px;height:190px" role="img" aria-label="Cherry gummies pouch with cherries"></div><div class="bar" style="background:var(--cherry)"></div></div>
  <div class="prod-name" style="margin-top:20px">Aurelia Delta 8 Gummies</div>
  <div class="prod-flavor" style="color:var(--cherry)">CHERRY</div>
  <div class="btn btn-outline" style="position:relative;margin:14px auto 0;width:110px;height:31px">Buy now</div>
</div>
<div class="abs" style="top:1355px;left:473px">
  <div class="card-img" style="position:relative"><div class="abs bag" style="top:58px;left:47px;width:160px;height:190px" role="img" aria-label="Blue raspberry gummies pouch with berries"></div><div class="bar" style="background:var(--berry)"></div></div>
  <div class="prod-name" style="margin-top:20px">Aurelia Delta 8 Gummies</div>
  <div class="prod-flavor" style="color:var(--berry)">BLUE RASPBERRY</div>
  <div class="btn btn-outline" style="position:relative;margin:14px auto 0;width:110px;height:31px">Buy now</div>
</div>
<div class="abs" style="top:1355px;left:756px">
  <div class="card-img" style="position:relative"><div class="abs bag" style="top:58px;left:47px;width:160px;height:190px" role="img" aria-label="Sour apple gummies pouch with green apples"></div><div class="bar" style="background:var(--apple)"></div></div>
  <div class="prod-name" style="margin-top:20px">Aurelia Delta 8 Gummies</div>
  <div class="prod-flavor" style="color:var(--apple)">SOUR APPLE</div>
  <div class="btn btn-outline" style="position:relative;margin:14px auto 0;width:110px;height:31px">Buy now</div>
</div>

<div class="abs benefits" role="img" aria-label="Faint circular pattern background"></div>
<h2 class="abs serif section-title center" style="top:1880px">AURELIA DELTA 8 GUMMIES BENEFITS</h2>
<p class="abs section-copy center" style="top:1928px">Lorem ipsum dolor sit amet, consectetur adipiscing elit, sed do eiusmod<br>sum dolor sit amet, consectetur adipiscing elit, sed d</p>

<div class="abs benefit" style="top:2010px;left:155px">
  <svg width="44" height="44" viewBox="0 0 44 44" fill="none" stroke="#c9a13b" stroke-width="1.6"><circle cx="22" cy="22" r="18" fill="#f2e36c" fill-opacity=".5"/><path d="M8 18c6 0 8 4 6 8s2 8 6 8M24 5c0 6 6 6 8 10s6 4 8 2"/></svg>
  <h3>Amet Consectetur</h3><p>Lorem ipsum dolor sit amet, consectetur ed do eiusmod sum dolor sit amet.</p>
</div>
<div class="abs benefit" style="top:2010px;left:383px">
  <svg width="44" height="44" viewBox="0 0 44 44" fill="#f2e36c" stroke="#c9a13b" stroke-width="1.6"><path d="M22 38L7 22a8 8 0 0 1 15-9 8 8 0 0 1 15 9z"/></svg>
  <h3>Lmet Knsectetur</h3><p>Lorem ipsum dolor sit amet, consectetur ed do eiusmod sum dolor sit amet.</p>
</div>
<div class="abs benefit" style="top:2010px;left:610px">
  <svg width="44" height="44" viewBox="0 0 44 44" fill="none" stroke="#c9a13b" stroke-width="1.6"><circle cx="22" cy="12" r="6" fill="#f2e36c"/><path d="M22 18v20M22 30c-6-6-12-4-14-2 4 6 10 6 14 2zM22 30c6-6 12-4 14-2-4 6-10 6-14 2z"/></svg>
  <h3>Amet Consectetur</h3><p>Lorem ipsum dolor sit amet, consectetur ed do eiusmod sum dolor sit amet.</p>
</div>
<div class="abs benefit" style="top:2010px;left:835px">
  <svg width="44" height="44" viewBox="0 0 44 44" fill="#f2e36c" stroke="#c9a13b" stroke-width="1.6"><path d="M22 4l5 12 13 1-10 8 3 13-11-7-11 7 3-13-10-8 13-1z"/></svg>
  <h3>Lmet Knsectetur</h3><p>Lorem ipsum dolor sit amet, consectetur ed do eiusmod sum dolor sit amet.</p>
</div>
<div class="btn gold-grad" style="top:2281px;left:535px;width:131px;height:37px">Buy now</div>

<div class="abs testimonial gold-grad"></div>
<h2 class="abs serif section-title center" style="top:2432px">TESTIMONIAL</h2>
<span class="abs serif" style="top:2478px;left:350px;font-size:46px;color:#fff;line-height:1">“</span>
<p class="abs center" style="top:2492px;font-size:12px;line-height:18px;color:var(--ink)">Duis autem vel eum iriure dolor in hendrerit in vulputate velit esse molestie consequat,<br>vel illum dolore eu feugiat nulla facilisis at vero eros et accumsan et iusto odio dignissim<br>qui blandit praesent luptatum zzril delenit augue duis dolore te feugait nulla facilisi.</p>
<p class="abs center" style="top:2568px;font-size:9.5px;font-weight:600;color:#fff">LENA MARSH, ADIPSING AMET</p>
<svg class="abs" style="top:2597px;left:567px" width="86" height="12" viewBox="0 0 86 12" fill="none" stroke="#555" stroke-width="1.2"><path d="M10 6H2M5 3L2 6l3 3M76 6h8M81 3l3 3-3 3"/><circle cx="24" cy="6" r="2.5" fill="#1d1d1d" stroke="none"/><circle cx="37" cy="6" r="2" fill="#777" stroke="none"/><circle cx="49" cy="6" r="2" fill="#777" stroke="none"/><circle cx="62" cy="6" r="2" fill="#777" stroke="none"/></svg>

<footer class="abs footer">
  <div class="abs" style="top:56px;left:157px;display:flex;align-items:center;gap:8px;font-size:15px;font-weight:600;letter-spacing:3px;color:var(--gold)"><i style="width:14px;height:14px;border-radius:50%;background:var(--gold)"></i>AURELIA</div>
  <p class="abs" style="top:132px;left:157px;width:320px;font-size:10.5px;line-height:18px">Sed diam nonummy nibh euismod tincidunt ut laoreet dolore magna aliquam erat volutpat widsi enim ad minim.</p>
  <div class="abs social" style="top:213px;left:161px"></div>
  <div class="abs social" style="top:213px;left:207px"></div>
  <div class="abs social" style="top:213px;left:252px"></div>
  <div class="abs flink" style="top:95px;left:782px">Home</div>
  <div class="abs flink" style="top:123px;left:782px">Our Story</div>
  <div class="abs flink" style="top:151px;left:782px">Shop</div>
  <div class="abs flink" style="top:179px;left:782px">Contact Us</div>
  <div class="abs" style="top:90px;left:911px;font-size:10.5px;font-weight:500;color:#fff">Aurelia Delta 8 Gummies</div>
  <svg class="abs" style="top:124px;left:911px" width="11" height="14" viewBox="0 0 11 14" fill="none" stroke="#e6c84a" stroke-width="1.3"><path d="M5.5 13S1 8 1 5a4.5 4.5 0 0 1 9 0c0 3-4.5 8-4.5 8z"/><circle cx="5.5" cy="5" r="1.6"/></svg>
  <p class="abs" style="top:120px;left:929px;width:110px;font-size:10px;line-height:15px">48 Lorem Lane, Suite 210, Meadowfield, ZZ 00000</p>
  <svg class="abs" style="top:182px;left:910px" width="12" height="12" viewBox="0 0 12 12" fill="none" stroke="#e6c84a" stroke-width="1.3"><path d="M2 1h3l1 3-2 1a7 7 0 0 0 3 3l1-2 3 1v3c-5 1-10-4-9-9z"/></svg>
  <div class="abs" style="top:180px;left:929px;font-size:10px">555-010-2468</div>
  <svg class="abs" style="top:206px;left:910px" width="12" height="10" viewBox="0 0 12 10" fill="none" stroke="#e6c84a" stroke-width="1.3"><rect x="1" y="1" width="10" height="8"/><path d="M1 1l5 4 5-4"/></svg>
  <div class="abs" style="top:203px;left:929px;font-size:10px">hello@aurelia-example.com</div>
</footer>
<div class="abs copyright">© 2021 Aurelia</div>

</body>
</html>
```